4th Generation Family Business Needs a New Card Design!

We are a family owned 4th Generation company. We are based in the Sydney, Australia area and we are desperately in need of a more modern and classy card. We are monumental masons who design, supply & erect lasting memorials throughout cemeteries in Sydney. Our customers are normally in a period of grieving. I have attached logo files that will need to be implemented on the card. Company was established 1935. Australian Owned and Operated. Card needs to be designed to PIXO.com specification.

Target Market(s)

Our target market is based upon people that a grieving for family members that have passed away. We also deal with alot of companies that own and operate cemeteries.

Industry/Entity Type

Business

Contact Information for Business Card

Simon Harcourt, Operations Manager, 0417293086, simon@harcourtmemorials.com.au
Lewis Harcourt, Director, 0491630572, lewis@harcourtmemorials.com.au
Phone # 02 9561 3048
Website: www.harcourtmemorials.com.au
Address: Suite 17, 8 Palfrey Lane, West Carlow, Sydney NSW 2156

Font styles to use
Serif
Decorative
Script

Requirements
Must have
• Would like to see the logo nicely implemented with a modern design. Embossed lettering would be a nice additive.

```html
<!DOCTYPE html>
<html lang="en">
<head>
<meta charset="utf-8">
<title>Harcourt Memorials – Business Card</title>
<link rel="stylesheet" href="https://fonts.googleapis.com/css2?family=Roboto:wght@400;700&display=swap">
<style>
  :root {
    --backdrop: #3a3a3a;
    --gold: #efc12f;
    --gold-text: #e8b92a;
    --ink: #1d1d1b;
    --paper: #ffffff;
    --grey-text: #4a4a4a;
    --rule: #8a8a8a;
  }
  * { box-sizing: border-box; margin: 0; padding: 0; }
  html, body { width: 1200px; height: 950px; overflow: hidden; }
  body {
    background: var(--backdrop);
    font-family: "Roboto", Arial, sans-serif;
    display: flex;
    flex-direction: column;
    align-items: center;
    justify-content: center;
    gap: 44px;
  }
  .card {
    position: relative;
    width: 640px;
    height: 391px;
    overflow: hidden;
  }
  /* Front */
  .card--front {
    background: var(--gold);
    display: flex;
    flex-direction: column;
    align-items: center;
    justify-content: center;
  }
  .brand {
    display: flex;
    align-items: center;
    gap: 12px;
    color: var(--ink);
    font-weight: 700;
    text-transform: uppercase;
    letter-spacing: 2px;
  }
  .brand__mark { width: 18px; height: 18px; background: currentColor; }
  .card--front .brand { font-size: 30px; margin-top: 10px; }
  .front__web {
    position: absolute;
    bottom: 56px;
    left: 0; right: 0;
    text-align: center;
    font-size: 15px;
    color: var(--ink);
  }
  /* Back */
  .card--back { background: var(--paper); }
  .back__tab {
    position: absolute;
    top: 0; right: 0;
    width: 14px; height: 44px;
    background: var(--ink);
  }
  .person {
    position: absolute;
    top: 46px; right: 40px;
    text-align: right;
    text-transform: uppercase;
  }
  .person__name { font-size: 22px; font-weight: 700; color: var(--ink); letter-spacing: .3px; }
  .person__role { font-size: 15px; color: var(--gold-text); margin-top: 2px; letter-spacing: .3px; }
  .back__rule {
    position: absolute;
    left: 40px; right: 40px; top: 150px;
    border-top: 1px solid var(--rule);
  }
  .address {
    position: absolute;
    top: 170px; right: 40px;
    text-align: right;
    font-style: normal;
    font-size: 15px;
    line-height: 1.45;
    color: var(--grey-text);
  }
  .card--back .brand {
    position: absolute;
    left: 40px; top: 200px;
    font-size: 22px;
    padding-bottom: 8px;
    border-bottom: 2px solid var(--gold);
  }
  .contacts {
    position: absolute;
    left: 40px; bottom: 30px;
    list-style: none;
    font-size: 15px;
    color: var(--grey-text);
  }
  .contacts li { display: flex; align-items: center; gap: 10px; line-height: 25px; }
  .contacts svg { width: 15px; height: 15px; fill: var(--ink); flex: none; }
</style>
</head>
<body>

<section class="card card--front" aria-label="Card front">
  <div class="brand"><span class="brand__mark"></span>Harcourt Memorials</div>
  <p class="front__web">www.harcourtmemorials.com.au</p>
</section>

<section class="card card--back" aria-label="Card back">
  <span class="back__tab"></span>
  <div class="person">
    <p class="person__name">Simon Harcourt</p>
    <p class="person__role">Operations Manager</p>
  </div>
  <div class="back__rule"></div>
  <address class="address">
    Suite 17<br>8 Palfrey Lane<br>West Carlow<br>Sydney NSW 2156
  </address>
  <div class="brand">Harcourt Memorials</div>
  <ul class="contacts">
    <li>
      <svg viewBox="0 0 16 16" aria-hidden="true"><path d="M2 5c0-2 2-3 6-3s6 1 6 3v1h-3V4.5H5V6H2z"/><rect x="3" y="7" width="10" height="7" rx="1"/></svg>
      02 9561 3048
    </li>
    <li>
      <svg viewBox="0 0 16 16" aria-hidden="true"><path d="M4.5 1h7a1 1 0 0 1 1 1v12a1 1 0 0 1-1 1h-7a1 1 0 0 1-1-1V2a1 1 0 0 1 1-1zm.5 2v9h6V3z"/></svg>
      0417293086
    </li>
    <li>
      <svg viewBox="0 0 16 16" aria-hidden="true"><path d="M1 3h14v10H1zm1.5 1.5v.3L8 8.6l5.5-3.8v-.3z"/></svg>
      simon@harcourtmemorials.com.au
    </li>
    <li>
      <svg viewBox="0 0 16 16" aria-hidden="true"><circle cx="8" cy="8" r="7"/><path d="M1 8h14M8 1c-3 3-3 11 0 14M8 1c3 3 3 11 0 14" stroke="#fff" stroke-width="1" fill="none"/></svg>
      www.harcourtmemorials.com.au
    </li>
  </ul>
</section>

</body>
</html>
```